lofty birch website

We need a new website for our new business division. We are a sustainable design firm specializing in servicing the needs if architects and developers. We have a staff consisting of architects, engineers, and former contractors and we understand green must make sense.

Bottomline - the only sustainable and lofty birch solutions are those thatbare good for the environment and good for our clients bottom line.

Our company is lofty birch and we will send you a copy of our logo you will see our tagline. Is simple. sustainable. solutions. The play with the periods is that we believe their are simple sustainable solutions and we want to use the words together and possible let each stand alone to accentuate their individual meaning in regards to benefit to our clients.

We want a cool splash page with nich graphics and pictures then later pages to feature projects and design ideas.

Target Market(s)

Our target customers are architects, developers, and contractors who would need assistance with the design process for a VARO project or assisatnce with a building owner who wants to make tehir facilty more environmentally friendly and save energy costs at the same tiem.

Industry/Entity Type

Environment

Requirements
Must have
• Needs a construction look with an environmentally friendly surrounding that is pleasing to look at. Must appeal to the client not only as environmentally friendly but also a wise investment.
Nice to have
• Opportunity for a connection to Social networking including a blog.
Should not have
• A totally environmental building feel at whatever cost. We want to emphasize that it is possible to build environmental friendly and save you money over the life of your building

```html
<!DOCTYPE html>
<html lang="en">
<head>
<meta charset="utf-8">
<title>Lofty Birch — simple. sustainable. solutions.</title>
<link rel="stylesheet" href="https://fonts.googleapis.com/css2?family=Arimo:wght@400;700&display=swap">
<style>
  :root {
    --green-deep: #1f7a10;
    --green: #2aa42a;
    --green-bright: #28d22a;
    --green-text: #1d8a1d;
    --page-bg: #ecfcec;
    --header-bg: #e4fbe4;
    --nav-dark: #2e2e2e;
    --nav-light: #5a5a5a;
    --grey-text: #555555;
    --ink: #111111;
    --footer-dark: #2b2b2b;
    --footer-light: #5c5c5c;
    --news-bg: #f2f2f2;
  }
  * { box-sizing: border-box; margin: 0; padding: 0; }
  html, body { width: 1200px; height: 1008px; overflow: hidden; }
  body {
    position: relative;
    font-family: "Arimo", Arial, sans-serif;
    color: var(--ink);
    background: linear-gradient(90deg, #2f7d08 0%, #5fb423 50%, #2f7d08 100%);
  }
  .page {
    position: absolute; left: 45px; top: 0; width: 1114px; height: 945px;
    background: var(--page-bg);
  }
  .site-header {
    position: absolute; left: 0; top: 0; width: 100%; height: 140px;
    background: linear-gradient(180deg, #d6f8d6 0%, var(--header-bg) 60%, #f4fff4 100%);
  }
  .brand { position: absolute; left: 18px; top: 32px; display: flex; align-items: flex-start; gap: 12px; }
  .brand-mark { width: 70px; height: 70px; background: var(--green); }
  .brand-name { font-size: 46px; font-weight: 700; color: var(--green-text); line-height: 1; letter-spacing: -1px; }
  .brand-tagline { font-size: 19px; color: var(--grey-text); margin-top: 4px; }
  .call-us { position: absolute; right: 15px; top: 60px; font-size: 22px; color: var(--ink); }
  .call-us strong { font-weight: 700; }

  .main-nav {
    position: absolute; left: 0; top: 140px; width: 100%; height: 41px;
    background: linear-gradient(180deg, var(--nav-light) 0%, var(--nav-dark) 100%);
    display: flex;
  }
  .main-nav a {
    display: block; height: 41px; line-height: 41px; color: #fff; text-decoration: none;
    font-weight: 700; font-size: 15px; text-align: center;
  }
  .main-nav a.is-active { background: linear-gradient(180deg, var(--green-bright), #16a418); }

  .hero { position: absolute; left: 0; top: 181px; width: 1114px; height: 387px; }
  .hero svg { display: block; }
  .hero-quote {
    position: absolute; right: 60px; top: 326px; text-align: center;
    font-size: 23px; font-weight: 700; color: #333; line-height: 30px;
  }
  .hero-quote em { font-style: normal; color: var(--green-text); }

  .welcome { position: absolute; left: 18px; top: 585px; width: 796px; }
  .welcome h1 { font-size: 32px; font-weight: 700; color: var(--green-text); line-height: 40px; }
  .welcome p { font-size: 13.8px; line-height: 18.4px; margin-top: 13px; }
  .welcome p + p { margin-top: 18px; }

  .projects { position: absolute; left: 18px; top: 768px; width: 796px; }
  .projects h2 { font-size: 23px; font-weight: 700; color: var(--grey-text); line-height: 26px; }
  .project-list { display: flex; gap: 22px; margin-top: 10px; }
  .project-thumb {
    width: 180px; height: 116px;
    background: linear-gradient(180deg, #1f56b8 0%, #6fa3d8 40%, #c9d3d6 62%, #8fa2a6 78%, #5f8a45 100%);
  }

  .sidebar-box { position: absolute; left: 835px; width: 262px; }
  .services { top: 591px; height: 168px; background: var(--green); }
  .services h3 {
    height: 33px; line-height: 33px; padding-left: 11px; color: #fff; font-size: 18px; font-weight: 700;
    background: linear-gradient(180deg, #16901a, var(--green-deep));
  }
  .services ul { list-style: none; padding: 8px 10px 0 14px; }
  .services li { color: #fff; font-weight: 700; font-size: 14px; line-height: 18px; margin-bottom: 7px; padding-left: 10px; text-indent: -10px; }
  .news { top: 784px; height: 138px; background: var(--news-bg); border: 1px solid #c8c8c8; }
  .news h3 {
    height: 32px; line-height: 32px; padding-left: 11px; color: #fff; font-size: 18px; font-weight: 700;
    background: linear-gradient(180deg, #888, #4a4a4a);
  }
  .news ul { list-style: none; padding: 7px 10px 0 13px; }
  .news li { font-size: 13.5px; line-height: 18.4px; padding-left: 9px; text-indent: -9px; }
  .news .more { position: absolute; right: 24px; bottom: 6px; font-size: 13.5px; font-weight: 700; color: #333; }

  .site-footer {
    position: absolute; left: 0; top: 945px; width: 1200px; height: 63px;
    background: linear-gradient(180deg, var(--footer-dark) 0%, var(--footer-light) 100%);
  }
  .site-footer p { position: absolute; left: 46px; top: 16px; color: #fff; font-size: 13.5px; }
</style>
</head>
<body>
  <div class="page">
    <header class="site-header">
      <div class="brand">
        <span class="brand-mark"></span>
        <div>
          <div class="brand-name">lofty birch</div>
          <div class="brand-tagline">simple. sustainable. solutions.</div>
        </div>
      </div>
      <div class="call-us">Call US : <strong>+555012 340</strong></div>
    </header>

    <nav class="main-nav">
      <a href="#" style="width:108px">HOME</a>
      <a href="#" class="is-active" style="width:138px">ABOUT US</a>
      <a href="#" style="width:162px">OUR SERVICES</a>
      <a href="#" style="width:150px">OUR CLIENT</a>
      <a href="#" style="width:100px">FAQ</a>
      <a href="#" style="width:140px">CONTACT US</a>
    </nav>

    <section class="hero">
      <svg width="1114" height="387" viewBox="0 0 1114 387">
        <defs>
          <linearGradient id="heroScene" x1="0" y1="0" x2="1" y2="0">
            <stop offset="0" stop-color="#3a8fd0"/>
            <stop offset="0.2" stop-color="#6cb8e6"/>
            <stop offset="0.42" stop-color="#9fc9ea"/>
            <stop offset="0.6" stop-color="#c4dcf1"/>
            <stop offset="0.8" stop-color="#a9cbea"/>
            <stop offset="1" stop-color="#7fb0e0"/>
          </linearGradient>
          <linearGradient id="heroFade" x1="0" y1="0" x2="0" y2="1">
            <stop offset="0" stop-color="#ffffff" stop-opacity="0"/>
            <stop offset="0.55" stop-color="#ffffff" stop-opacity="0.25"/>
            <stop offset="1" stop-color="#e9eef2" stop-opacity="0.7"/>
          </linearGradient>
        </defs>
        <g role="img" aria-label="Photo of two engineers in yellow hard hats beside a glass building, with a sketched city skyline against a cloudy sky">
          <rect width="1114" height="387" fill="url(#heroScene)"/>
          <rect width="1114" height="387" fill="url(#heroFade)"/>
        </g>
        <path d="M0 300 C 200 360, 420 340, 620 300 C 820 262, 980 250, 1114 266 L1114 387 L0 387 Z" fill="#4a4a4a"/>
        <path d="M0 322 C 180 380, 430 360, 640 318 C 840 280, 990 272, 1114 290 L1114 387 L0 387 Z" fill="#2aa42a"/>
        <path d="M0 348 C 200 400, 440 378, 660 340 C 860 306, 1000 300, 1114 312 L1114 387 L0 387 Z" fill="#ecfcec"/>
      </svg>
      <div class="hero-quote">“<em>Affordable</em> and <em>effective</em> solution<br>for your Developer &amp; Architect”</div>
    </section>

    <section class="welcome">
      <h1>Welcome to Lofty Birch</h1>
      <p>Lorem ipsum dolor sit amet, consectetur adipiscing elit. Vestibulum vitae libero et ligula consequat ullamcorper eget vel purus.<br>Proin pellentesque sapien magna. Mauris venenatis tortor non purus facilisis dignissim. Nunc quis lectus sit amet ante luctus<br>congue sit amet non mauris.</p>
      <p>Etiam a sem leo, a pellentesque nisl. Fusce sit amet ultricies ante. Aliquam erat volutpat. Aenean in mauris arcu, quis vehicula<br>augue. Nam lacinia condimentum sapien id suscipit.</p>
    </section>

    <section class="projects">
      <h2>Feauter Projects</h2>
      <div class="project-list">
        <div class="project-thumb" role="img" aria-label="Modern office building project"></div>
        <div class="project-thumb" role="img" aria-label="Modern office building project"></div>
        <div class="project-thumb" role="img" aria-label="Modern office building project"></div>
        <div class="project-thumb" role="img" aria-label="Modern office building project"></div>
      </div>
    </section>

    <aside class="sidebar-box services">
      <h3>OUR SERVICES</h3>
      <ul>
        <li>• Lorem ipsum dolor sit amet,<br>Morbi in est vel est mollis.</li>
        <li>• Lorem ipsum dolor sit amet,<br>Morbi in est vel est mollis.</li>
        <li>• Lorem ipsum dolor sit amet,<br>Morbi in est vel est mollis.</li>
      </ul>
    </aside>

    <aside class="sidebar-box news">
      <h3>Letest News..</h3>
      <ul>
        <li>• Lorem ipsum dolor sit amet,<br>Morbi in est vel est mollis.</li>
        <li>• Lorem ipsum dolor sit amet,<br>Morbi in est vel est mollis.</li>
      </ul>
      <span class="more">More...</span>
    </aside>
  </div>

  <footer class="site-footer">
    <p>Footer Text Here</p>
  </footer>
</body>
</html>
```